Corvane Business Cards

Front of business card will have logo, name, address, & telephone number. Back of card will have a list of services provided - Roads, Substation Pads, Temporary Pads, Site Pads, Land Leveling, Powerline Row Cleaning, Land Clearing, Gates, Fencing, Construction Entrances, Excavation, Trenching, Underground Utilities, Directional Boring, Pile Driving. We are a construction company that uses heavy equipment like bulldozers, motor graders/blades, dump trucks, backhoes, hydro axes, & skid loaders. We build roads, pads, & install electric utility lines & waterlines underground. This logo is new. The word "Construction" can be smaller as uploaded 2 example edited logos. We will be using this card design for many employees.
Target Market(s)
Industrial Electric Powerline, Wind Turbine, Solar Panel, & Water Utility companies.
Contact Information for Business Card
Name/Position - Dwayne Halster - Owner
Address: 4875 FM 309
Merkel, TX 79412
Phone number - (325) 482-5096

```html
<!DOCTYPE html>
<html lang="en">
<head>
<meta charset="utf-8">
<title>Corvane Construction Business Cards</title>
<link href="https://fonts.googleapis.com/css2?family=Roboto:wght@400;500;700&display=swap" rel="stylesheet">
<style>
  :root {
    --maroon: #3e111b;
    --maroon-ink: #4a1520;
    --paper: #ffffff;
    --text-grey: #4a4a4a;
    --stage: #d9d6d4;
  }
  * { box-sizing: border-box; margin: 0; padding: 0; }
  html, body { width: 1200px; height: 900px; overflow: hidden; }
  body {
    background: var(--stage);
    font-family: 'Roboto', sans-serif;
    display: flex;
    flex-direction: column;
    align-items: center;
    justify-content: center;
    gap: 40px;
  }
  .card {
    width: 700px;
    height: 400px;
    position: relative;
    box-shadow: 0 6px 18px rgba(0,0,0,0.25);
  }

  /* Back: services */
  .card-back {
    background: var(--maroon);
    color: var(--paper);
    display: flex;
    flex-direction: column;
    align-items: center;
    padding-top: 105px;
  }
  .card-back .brand {
    font-size: 64px;
    font-weight: 700;
    letter-spacing: 2px;
    line-height: 1;
    color: var(--paper);
  }
  .services {
    margin-top: 70px;
    list-style: none;
    text-align: center;
    font-size: 14.5px;
    line-height: 1.55;
    letter-spacing: 0.2px;
  }

  /* Front: contact */
  .card-front { background: var(--paper); color: var(--maroon-ink); }
  .brand-block {
    position: absolute;
    top: 62px;
    right: 70px;
    text-align: center;
    font-weight: 700;
    color: var(--maroon-ink);
  }
  .brand-block .name { font-size: 46px; letter-spacing: 2px; line-height: 1; }
  .brand-block .tag { font-size: 30px; letter-spacing: 3px; margin-top: 8px; line-height: 1; }
  .rule {
    position: absolute;
    left: 250px;
    right: 40px;
    top: 262px;
    height: 1.5px;
    background: var(--maroon-ink);
  }
  .person { position: absolute; left: 48px; top: 238px; }
  .person .full-name {
    font-size: 22px; font-weight: 700; letter-spacing: 0.5px; line-height: 26px; color: var(--maroon-ink);
  }
  .person .role { font-size: 18px; color: var(--text-grey); margin-top: 2px; }
  .contact {
    position: absolute;
    display: flex;
    align-items: center;
    gap: 8px;
    font-size: 19px;
    color: var(--text-grey);
    white-space: nowrap;
  }
  .contact svg { width: 16px; height: 16px; fill: var(--maroon-ink); flex: none; }
  .contact-phone { left: 48px; top: 335px; }
  .contact-address { right: 40px; top: 286px; }
</style>
</head>
<body>
  <section class="card card-back">
    <div class="brand">CORVANE</div>
    <ul class="services">
      <li>Roads | Substation Pads | Temporary Pads | Site Pads | Land Leveling</li>
      <li>Land Clearing | Gates | Fencing | Construction Entrances | Excavation | Trenching</li>
      <li>Underground Utilities | Powerline Row Cleaning | Pile Driving | Directional Boring</li>
    </ul>
  </section>

  <section class="card card-front">
    <div class="brand-block">
      <div class="name">CORVANE</div>
      <div class="tag">CONSTRUCTION</div>
    </div>
    <div class="rule"></div>
    <div class="person">
      <div class="full-name">DWAYNE HALSTER</div>
      <div class="role">Owner</div>
    </div>
    <div class="contact contact-phone">
      <svg viewBox="0 0 24 24" aria-hidden="true"><path d="M6.6 10.8a15.1 15.1 0 0 0 6.6 6.6l2.2-2.2a1 1 0 0 1 1-.25 11.4 11.4 0 0 0 3.6.57 1 1 0 0 1 1 1V20a1 1 0 0 1-1 1A17 17 0 0 1 3 4a1 1 0 0 1 1-1h3.5a1 1 0 0 1 1 1c0 1.25.2 2.45.57 3.6a1 1 0 0 1-.25 1z"/></svg>
      <span>(325) 482-5096</span>
    </div>
    <div class="contact contact-address">
      <svg viewBox="0 0 24 24" aria-hidden="true"><path d="M12 2a7 7 0 0 0-7 7c0 5.2 7 13 7 13s7-7.8 7-13a7 7 0 0 0-7-7zm0 9.5A2.5 2.5 0 1 1 12 6.5a2.5 2.5 0 0 1 0 5z"/></svg>
      <span>4875 FM 309 Dunmore Flats, TX 79412</span>
    </div>
  </section>
</body>
</html>
```